Church Website with Home Page and Member Sermon Library

I am in need of an updated design for our church website. This will include 4 pages (outlined below). We are a conservative, evangelical, Christian church. The site should be modern and clean, while still reflecting our conservative values. I already have a logo for our church, and I want the site to incorporate the logo, and match the logo/branding. Stock photos are allowed if needed, but I have uploaded some images of our church and would prefer those images to be used if possible. Any stock photos used should not include any people in the photos (scenery, nature, buildings, animals, etc. are fine).

The site will need 4 pages: Home, Support Us (Donate), Login, and Recording Library.

Page 1: Home
The home page should include the following sections:

- Navigation: Should include links to each section of the home page plus a "listen live" link which will take the user to a live-streaming site and a "support us" link which will take the user to a support/donate page.

- Announcements: Can be either a banner or some other design, but there needs to be some way for us to post announcements for visitors to see. I'm open for creative ideas in this section, but would like it not to take up a lot of room on the page.

- About Us: Should include address, service times (see attached document), and information about the church.

- Pastor Bio: A section that introduces our pastor and gives a short bio about our pastor. Would like this section to include a picture of our pastor. Somewhere in this section I would like to include this Bible reference: "And I will give you pastors according to mine heart, which shall feed you with knowledge and understanding. Jer 3:15 LPW"

- Articles of Faith (What We Believe): This should include several sub-sections each with a heading, body, and possibly 1 or more scripture references. I have attached a document to the brief that includes our articles of faith. Feel free to be creative with this section in how you lay these out and format them.

- Support Us: A small section that explains what kind of support someone can give and a link to a donation page. The link can say something like "Support Us" or "Donate Now".

- Contact form: A contact form that allows the visitor to send us a message. The contact form should ask for name, email, phone, and message.

- Footer: A footer that will be displayed on all pages of the site. This should include at a minimum a link to the home page (or a link to each individual section in the home page if you prefer), a link to "listen live", a link to "support us", a link to "contact us" (or you can put the contact form directly in the footer if you prefer), the address, and a "member login" link.

Page 2: Support Us
The donation page should include a form the visitor can fill out to make a donation. We will embed a third party form later. For this design, please just mock out the design with a basic form asking for name, phone, and email.

Page 3: Login
The recording library (detailed below) will require members to login with a shared numeric code before accessing the page. We need a design for a login screen. The screen should include navigation/footer just like all other pages, but the body of the login page will consist only of a form that asks the user to enter the access code and then a "login" button.

Page 4: Recording Library

The library page is a member-only page that will require a shared, numeric pass code to access. On this page, members will be able to access a filterable list of past sermons. The page by default should display most recent sermons, but should also include a search form that allows the member to filter the sermon list to find a particular sermon. The search form should allow the user to select a filter type (e.g. Speaker name, date, event, etc.) and type in a value to search. They should be able to add multiple filters and remove filters that have been added. Each sermon that is displayed in the result list should include basic information such as title, date, speaker, tags, etc. along with a download icon, and an embedded audio player where they can click a play button to stream it on-demand. Each sermon should also have clickable tags associated with it that can be used to find related sermons.
Updates

I have uploaded several images of our church. Feel free to incorporate these into your design if possible.

Target Market(s)

Church Members

Industry/Entity Type

Religion

Number of Pages Required

4 page

Font styles to use
Sans Serif

Colors

Designer to choose colors to be used in the design.

Requirements
Must have
• Must incorporate the logo (attached)
Nice to have
• Would like the design to incorporate pictures of our church (attached) instead of stock photos if possible.
Should not have
• Please avoid an overly cluttered design. Stock photos used should not include any people in the photos.

```html
<!DOCTYPE html>
<html lang="en">
<head>
<meta charset="utf-8">
<title>Grace Hill Chapel</title>
<link href="https://fonts.googleapis.com/css2?family=Cinzel:wght@400;500;600;700&family=Montserrat:ital,wght@0,400;0,500;0,600;1,500;1,600&display=swap" rel="stylesheet">
<style>
:root{
  --green:#7ea56a;
  --teal:#23aac6;
  --slate:#4a6b85;
  --slate-light:#93a8ba;
  --ink:#1f1f1f;
  --text:#555;
  --muted:#777;
  --panel:#efefef;
  --footer:#333333;
  --field:#3d3d3d;
}
*{margin:0;padding:0;box-sizing:border-box}
html,body{width:1200px;height:3708px;overflow:hidden;background:#fff}
body{font-family:"Montserrat",sans-serif;color:var(--text)}
.page{position:relative;width:1200px;height:3708px;overflow:hidden}
.abs{position:absolute}
.serif{font-family:"Cinzel",serif}

/* hero */
.hero-photo{left:0;top:0;width:1200px;height:584px;
  background:
   linear-gradient(90deg,#fff 0%,rgba(255,255,255,.85) 10%,rgba(255,255,255,.1) 35%,rgba(255,255,255,0) 60%),
   linear-gradient(180deg,#f7f2e8 0%,#efe6d6 45%,#d8c6a8 70%,#a87b4f 85%,#c7a77f 100%)}
.brand{font-family:"Cinzel",serif;color:var(--green);text-align:center;letter-spacing:2px;line-height:1}
.brand-hero{left:130px;top:60px;width:160px;font-size:26px}
.brand-hero small{display:block;font-size:10px;letter-spacing:7px;margin-top:6px}
.brand-mark{width:22px;height:22px;border-radius:50%;background:var(--teal);margin:0 auto 10px}
.nav{left:528px;top:66px;display:flex;gap:35px;font-size:14px;color:var(--ink)}
.btn-donate{background:var(--green);color:#fff;font-family:"Cinzel",serif;font-size:15px;letter-spacing:1px;display:flex;align-items:center;justify-content:center}
.hero-donate{left:930px;top:57px;width:99px;height:35px}
.hero-title{left:0;width:1200px;top:270px;text-align:center;font-family:"Cinzel",serif;font-size:54px;letter-spacing:5px;color:var(--ink);font-weight:400}
.hero-rule{left:518px;top:347px;width:163px;height:3px;background:var(--ink)}
.hero-lede{left:300px;width:600px;top:373px;text-align:center;font-size:15px;line-height:22px;color:var(--ink)}

/* about */
.arch-outline{left:120px;top:600px}
.arch-photo{left:158px;top:691px;width:318px;height:477px;
  clip-path:path("M0,477 L0,220 C0,130 80,50 159,0 C238,50 318,130 318,220 L318,477 Z");
  background:linear-gradient(180deg,#dcd6cc 0%,#cfc7b8 50%,#b48654 82%,#8a5a32 100%)}
.eyebrow{font-family:"Cinzel",serif;font-size:14px;letter-spacing:1.5px;color:var(--ink)}
.h2{font-family:"Cinzel",serif;font-weight:400;color:var(--ink);letter-spacing:3px}
.about-eyebrow{left:573px;top:658px}
.about-title{left:573px;top:686px;font-size:36px;line-height:41px;width:400px}
.about-copy{left:573px;top:816px;width:450px;font-size:13px;line-height:21.5px}
.about-copy p+p{margin-top:14px}
.blue-rule{left:573px;top:980px;width:151px;height:2px;background:var(--teal)}
.blue-rule::after{content:"";position:absolute;left:0;top:6px;width:75px;height:1px;background:var(--teal)}
.times-title{left:573px;top:1010px}
.times{left:573px;top:1049px;list-style:none;font-family:"Cinzel",serif;font-size:13px;color:var(--ink);letter-spacing:1px}
.times li{height:36px}
.times .n{color:var(--green);margin-right:8px}
.times b{font-weight:700}

/* announcement */
.ann-frame{left:170px;top:1200px}
.ann-badge{left:540px;top:1212px;width:124px;font-size:17px}
.ann-badge .brand-mark{width:16px;height:16px;margin-bottom:8px}
.ann-badge small{display:block;font-size:7px;letter-spacing:4px;margin-top:4px}
.ann-title{left:0;width:1200px;top:1344px;text-align:center;font-size:38px}
.ann-text{left:310px;width:580px;top:1393px;text-align:center;font-size:13.5px;line-height:22px;color:var(--ink)}
.ann-label{left:330px;width:241px;top:1463px;text-align:right}
.ann-label .big{font-family:"Cinzel",serif;font-size:19px;letter-spacing:2px;color:var(--ink)}
.ann-label .date{font-family:"Cinzel",serif;font-size:11px;letter-spacing:1px;color:var(--ink);margin-top:12px}
.ann-divider{left:593px;top:1461px;width:1px;height:54px;background:var(--ink)}
.ann-from{left:617px;top:1462px;font-family:"Cinzel",serif;font-size:13px;letter-spacing:1.5px;line-height:14px;color:var(--ink)}
.ann-from i{display:block;font-family:"Montserrat",sans-serif;font-size:12px;letter-spacing:0;margin-top:8px}

/* pastor */
.pastor-eyebrow{left:0;width:1200px;text-align:center;top:1665px}
.pastor-title{left:0;width:1200px;text-align:center;top:1690px;font-size:35px;line-height:41px}
.pastor-col{width:250px;font-size:13px;line-height:21.5px}
.pastor-col p+p{margin-top:16px}
.pastor-left{left:171px;top:1845px}
.pastor-right{left:768px;top:1845px}
.pastor-photo{left:466px;top:1817px;width:266px;height:266px;border-radius:50%;
  background:radial-gradient(circle at 50% 40%,#e9e3d8 0%,#cfc6b6 45%,#3a3634 75%,#262322 100%)}
.read-bio{left:768px;top:2030px;font-family:"Cinzel",serif;font-size:14px;color:var(--green);letter-spacing:.5px;padding-bottom:6px;border-bottom:1px solid var(--green);width:112px}
.quote-mark{left:585px;top:2102px}
.quote{left:350px;width:500px;top:2129px;text-align:center;font-style:italic;font-weight:600;font-size:13px;line-height:20px;color:var(--ink)}
.quote-role{left:0;width:1200px;top:2178px;text-align:center;font-style:italic;font-size:9px;color:var(--muted)}
.quote-name{left:0;width:1200px;top:2196px;text-align:center;font-family:"Cinzel",serif;font-size:15px;letter-spacing:.5px;color:var(--ink)}

/* live */
.live-line{top:2326px;height:3px;width:189px;background:linear-gradient(90deg,rgba(74,107,133,0),var(--slate))}
.live-line.right{background:linear-gradient(90deg,var(--slate),rgba(74,107,133,0))}
.live-pill{left:409px;top:2292px;width:382px;height:72px;border-radius:36px;background:#f7f7f7;box-shadow:0 4px 14px rgba(0,0,0,.12);display:flex;align-items:center;padding-left:18px}
.live-icon{width:50px;height:50px;border-radius:50%;background:#fff;display:flex;align-items:center;justify-content:center;margin-right:24px}
.live-pill span{font-family:"Cinzel",serif;font-weight:600;font-size:14px;color:var(--green);letter-spacing:.5px}

/* articles */
.articles-bg{left:0;top:2442px;width:1200px;height:861px;
  background:radial-gradient(ellipse at 50% 40%,rgba(255,255,255,.95) 0%,rgba(255,255,255,.7) 45%,rgba(255,255,255,0) 80%),
  linear-gradient(180deg,#f3f0ef 0%,#ece7e6 50%,#dcd5d2 100%)}
.articles-title{left:0;width:1200px;top:2516px;text-align:center;font-size:36px}
.article h3{font-family:"Cinzel",serif;font-weight:400;font-size:17px;letter-spacing:1.5px;color:var(--ink);line-height:20px}
.article h3::before{content:"";display:inline-block;width:5px;height:5px;border-radius:50%;background:var(--green);margin-right:11px;vertical-align:3px}
.article p{font-size:12px;line-height:20px;color:var(--text);margin-top:11px}
.article p+p{margin-top:8px}
.left-col .article{width:373px;left:178px}
.right-col .article{width:392px;left:630px}
.divide{height:1px;background:#d9d2d0}
.left-col .divide{left:178px;width:373px}
.right-col .divide{left:630px;width:392px}
.scripture{list-style:none;margin-top:16px;font-size:9.5px;color:var(--ink)}
.scripture li{height:23.5px}
.scripture b{font-family:"Cinzel",serif;font-weight:600;font-size:12px;color:var(--green);margin-right:9px}

/* footer */
.footer{left:0;top:3303px;width:1200px;height:405px;background:var(--footer)}
.brand-foot{left:181px;top:3380px;width:200px;font-size:34px}
.brand-foot .brand-mark{width:30px;height:30px;margin-bottom:18px}
.brand-foot small{display:block;font-size:12px;letter-spacing:10px;margin-top:8px}
.foot-text{left:150px;width:262px;top:3531px;text-align:center;font-size:12px;line-height:19px;color:#c9c9c9}
.foot-donate{left:236px;top:3583px;width:98px;height:34px}
.contact-title{left:594px;top:3360px;font-family:"Cinzel",serif;font-size:18px;letter-spacing:1.5px;color:#eee}
.field{border:1px solid #8a8a8a;background:var(--field);color:#ddd;font-size:12px;padding:10px 11px}
.send{left:594px;top:3591px;font-family:"Cinzel",serif;font-size:14px;color:var(--green);letter-spacing:.5px;display:flex;align-items:center;gap:8px}
.copyright{left:180px;top:3669px;font-size:11.5px;color:#e4e4e4}
.social{left:921px;top:3670px;display:flex;gap:15px}
.social span{width:11px;height:11px;border-radius:50%;background:#fff;display:block}
</style>
</head>
<body>
<div class="page">

  <!-- HERO -->
  <div class="abs hero-photo" role="img" aria-label="Bright church sanctuary with stained glass windows, altar and wooden pews"></div>
  <div class="abs brand brand-hero"><div class="brand-mark"></div>GRACE HILL<small>CHAPEL</small></div>
  <nav class="abs nav"><span>Home</span><span>About</span><span>Our Pastor</span><span>Articles Of Faith</span></nav>
  <div class="abs btn-donate hero-donate">DONATE</div>
  <h1 class="abs hero-title">KEEP FAITH ALWAYS</h1>
  <div class="abs hero-rule"></div>
  <p class="abs hero-lede">Lorem ipsum dolor sit amet consectetur cursus egestas turpis turpis enim et amet sed magna.</p>

  <!-- ABOUT -->
  <svg class="abs arch-outline" width="398" height="560" viewBox="0 0 398 560" aria-hidden="true">
    <path d="M8,560 L8,270 C8,160 110,70 199,8 C288,70 390,160 390,270 L390,560" fill="none" stroke="#ececec" stroke-width="8"/>
    <path d="M24,560 L24,275 C24,172 118,90 199,32 C280,90 374,172 374,275 L374,560" fill="none" stroke="#f3f3f3" stroke-width="3"/>
  </svg>
  <div class="abs arch-photo" role="img" aria-label="Tall arched church nave with rows of wooden chairs leading to the altar"></div>
  <div class="abs eyebrow about-eyebrow">ABOUT</div>
  <h2 class="abs h2 about-title">WELCOME TO GRACE HILL CHAPEL</h2>
  <div class="abs about-copy">
    <p>Ut diam tortor consectetur lacus scelerisque tortor congue viverra egestas. Tristique in consectetur leo arcu blandit diam et sed volutpat.</p>
    <p>Aliquam at commodo venenatis quis. Velit neque interdum molestie risus consectetur vestibulum a eget. Ultricies volutpat orci eros quisque ullamcorper quis est.</p>
  </div>
  <div class="abs blue-rule"></div>
  <div class="abs eyebrow times-title">SERVICE TIME ARE</div>
  <ul class="abs times">
    <li><span class="n">01.</span>TRADITIONAL WORSHIP SERVICES: <b>09:00 AM - 11:05 AM</b></li>
    <li><span class="n">02.</span>TRADITIONAL WORSHIP SERVICES: <b>09:00 AM - 11:05 AM</b></li>
    <li><span class="n">03.</span>TRADITIONAL WORSHIP SERVICES: <b>09:00 AM - 11:05 AM</b></li>
  </ul>

  <!-- ANNOUNCEMENT -->
  <svg class="abs ann-frame" width="860" height="370" viewBox="0 0 860 370" aria-hidden="true">
    <rect x="14" y="64" width="831" height="287" fill="none" stroke="var(--slate-light)" stroke-width="2.5"/>
    <path d="M7,101 A45,45 0 0 0 52,56 L370,56 A62,62 0 0 0 494,56 L807,56 A45,45 0 0 0 852,101 L852,313 A45,45 0 0 0 807,358 L52,358 A45,45 0 0 0 7,313 Z" fill="var(--panel)" stroke="var(--slate)" stroke-width="5"/>
  </svg>
  <div class="abs brand ann-badge"><div class="brand-mark"></div>GRACE HILL<small>CHAPEL</small></div>
  <h2 class="abs h2 ann-title">ANNOUNCEMENT BANNER SPOT</h2>
  <p class="abs ann-text">Ullamcorper facilisi egestas semper fames suscipit penatibus amet. Ut diam tortor consectetur lacus scelerisque tortor congue viverra</p>
  <div class="abs ann-label"><div class="big">ANNOUNCEMENT</div><div class="date">FABRUARY 16TH</div></div>
  <div class="abs ann-divider"></div>
  <div class="abs ann-from">GRACE HILL<br>CHAPEL<i>Pastor Sam Ortega</i></div>

  <!-- PASTOR -->
  <div class="abs eyebrow pastor-eyebrow">OUR PASTOR</div>
  <h2 class="abs h2 pastor-title">A MAN OF PRAYER AND HIGH<br>SPIRITUALITY</h2>
  <div class="abs pastor-col pastor-left">
    <p>Ullamcorper facilisi egestas semper fames suscipit penatibus amet. Ut diam tortor consectetur lacus scelerisque tortor congue viverra egestas. Tristique in consectetur leo arcu blandit diam et sed volutpat.</p>
    <p>Aliquam at commodo venenatis quis. Velit neque interdum molestie risus consectetur vestibulum a eget.</p>
  </div>
  <div class="abs pastor-photo" role="img" aria-label="Portrait of the pastor in dark clerical clothing holding a Bible"></div>
  <div class="abs pastor-col pastor-right">
    <p>Ut diam tortor consectetur lacus scelerisque tortor congue viverra egestas. Tristique in consectetur leo arcu blandit diam et sed volutpat.</p>
    <p>Aliquam at commodo venenatis quis. Velit neque interdum molestie risus consectetur vestibulum a eget.</p>
  </div>
  <div class="abs read-bio">READ FULL BIO</div>
  <svg class="abs quote-mark" width="26" height="18" viewBox="0 0 26 18" aria-hidden="true">
    <path d="M0,18 V9 C0,3 3,0 9,0 V4 C6,4 5,6 5,8 H10 V18 Z M14,18 V9 C14,3 17,0 23,0 V4 C20,4 19,6 19,8 H24 V18 Z" fill="var(--green)"/>
  </svg>
  <p class="abs quote">Aliquam at commodo venenatis quis. Velit neque interdum molestie risus consectetur vestibulum a eget.</p>
  <div class="abs quote-role">Pastor</div>
  <div class="abs quote-name">Marion Keller</div>

  <!-- LIVE -->
  <div class="abs live-line" style="left:171px"></div>
  <div class="abs live-line right" style="left:839px"></div>
  <div class="abs live-pill">
    <div class="live-icon">
      <svg width="34" height="34" viewBox="0 0 34 34" aria-hidden="true">
        <circle cx="17" cy="13" r="2.5" fill="#333"/>
        <path d="M12,8 A7,7 0 0 0 12,18 M22,8 A7,7 0 0 1 22,18 M8,5 A11,11 0 0 0 8,21 M26,5 A11,11 0 0 1 26,21" fill="none" stroke="#333" stroke-width="1.6" stroke-linecap="round"/>
        <rect x="8" y="25" width="18" height="8" rx="2" fill="var(--green)"/>
        <text x="17" y="31.3" text-anchor="middle" font-family="Montserrat,sans-serif" font-size="5.5" font-weight="600" fill="#fff">LIVE</text>
      </svg>
    </div>
    <span>LISTEN LIVE STREAMING SERVICES</span>
  </div>

  <!-- ARTICLES OF FAITH -->
  <div class="abs articles-bg" role="img" aria-label="Softly blurred church interior with pews"></div>
  <h2 class="abs h2 articles-title">ARTICLES OF FAITH</h2>

  <div class="left-col">
    <div class="abs article" style="top:2610px">
      <h3>FULL SALVATION.</h3>
      <p>We believe that Salvation is received only when a person comes to the realization that he or she is lost and separated from God and becomes full of godly sorrow, confessing their sins and true repentance, believing in the shed blood of the Lord Jesus Christ as the only sacrifice for sins. Through the blood of Christ we have:</p>
      <ul class="scripture">
        <li><b>01.</b>Remission of sins, Matthew 26:28 Heb 9:22</li>
        <li><b>02.</b>Sanctification. Hebrews 13:12</li>
        <li><b>03.</b>Redemption. Revelations 5:9</li>
        <li><b>04.</b>Cleansing. 1 John 1:7 Rev. 1:5</li>
        <li><b>05.</b>Justification. Romans 5:9</li>
      </ul>
    </div>
    <div class="abs divide" style="top:2915px"></div>
    <div class="abs article" style="top:2941px">
      <h3>SANCTIFICATION</h3>
      <p>“Sanctify them through thy truth thy word is truth St John 17:17. For this is the will of God even your sanctification”</p>
      <p>We believe in a set apart life, separate from the world to Christ 2 Cor 6:17-18</p>
    </div>
    <div class="abs divide" style="top:3084px"></div>
    <div class="abs article" style="top:3112px">
      <h3>SECOND COMING OF CHRIST.</h3>
      <p>We believe in the second coming of Jesus Christ. Matthew 24:44 Luke 12:40</p>
    </div>
  </div>

  <div class="right-col">
    <div class="abs article" style="top:2610px">
      <h3>BAPTISM OF THE HOLY GHOST.</h3>
      <p>We believe in the baptism of the Holy Ghost as it is taught in the Bible and promised by our Lord Jesus Christ, with speaking in tongues as the Spirit gives utterance as the initial evidence. Acts 2:4 we believe that the gift of the Holy Ghost is for all believers as the Lord promised. Acts 2:17-18</p>
    </div>
    <div class="abs divide" style="top:2766px"></div>
    <div class="abs article" style="top:2793px">
      <h3>ETERNITY</h3>
      <p>We believe in Literal Eternity. Eternal Life for the believer and eternal death for those without Christ. Revelations 21:1-27</p>
    </div>
    <div class="abs divide" style="top:2888px"></div>
    <div class="abs article" style="top:2915px">
      <h3>DIVINE HEALING.</h3>
      <p>We believe Divine Healing to be included in the atonement of Jesus Christ our Lord, And believe that it is still for us today. 1 Peter 2:24 Luke 9:1-2 Mark 16-18 James 5:15</p>
    </div>
    <div class="abs divide" style="top:3032px"></div>
    <div class="abs article" style="top:3057px">
      <h3>THE GOD HEAD.</h3>
      <p>We believe in the God head bodily, known as the Divine Trinity. This body consist of God the father, Jesus Christ, his only begotten son and the redeemer of the world, and of the Holy Ghost, The third person of the Divine Trinity</p>
    </div>
  </div>

  <!-- FOOTER -->
  <footer class="abs footer"></footer>
  <div class="abs brand brand-foot"><div class="brand-mark"></div>GRACE HILL<small>CHAPEL</small></div>
  <p class="abs foot-text">Aliquam at commodo venenatis quis. Velit neque interdum molestie risus.</p>
  <div class="abs btn-donate foot-donate">DONATE</div>

  <div class="abs contact-title">CONTACT US</div>
  <div class="abs field" style="left:594px;top:3403px;width:209px;height:34px">Name</div>
  <div class="abs field" style="left:815px;top:3403px;width:207px;height:34px">Phone</div>
  <div class="abs field" style="left:594px;top:3449px;width:428px;height:34px">Email address</div>
  <div class="abs field" style="left:594px;top:3494px;width:428px;height:76px">Message</div>
  <div class="abs send">SEND US
    <svg width="22" height="8" viewBox="0 0 22 8" aria-hidden="true"><path d="M0,4 H20 M16,1 L20,4 L16,7" fill="none" stroke="var(--green)" stroke-width="1.2"/></svg>
  </div>

  <div class="abs copyright">Copyright 2023 Grace Hill Chapel I All rights reserved</div>
  <div class="abs social" aria-label="Social links"><span></span><span></span><span></span><span></span></div>

</div>
</body>
</html>
```